Ridgeline Haul Carriers - Website

A clean, not cluttered informative website for our business. We specialize in the transportation of radioactive materials across North America. The site is mostly for information about our company and will not be used to attract business but will be used to attract employee's mainly drivers. Driver's are very hard to find in our area. One of the pages needs to be a job's posting page with an apply now button. Either an application can be filled out there or a resume can be uploaded which ever functionality works better. I would like a website that I can easily edit, ability to change text and photos.

Number of Pages Required

5+ page

Colors

Designer to choose colors to be used in the design.

Requirements
Must have
• Home - About - Services - Jobs - Contact pages
• A way prospective employee's can apply or upload their resume to be emailed to me
• Very clean apperance
Should not have
• I don't want it to be busy

```html
<!DOCTYPE html>
<html lang="en">
<head>
<meta charset="utf-8">
<title>Ridgeline Haul Carriers</title>
<link href="https://fonts.googleapis.com/css2?family=Lato:wght@400;700;900&display=swap" rel="stylesheet">
<style>
:root{
  --red:#e52629;
  --dark:#2a2a2a;
  --ink:#3a3a3a;
  --grey:#6d6d6d;
  --light:#f4f4f4;
  --white:#ffffff;
  --btn-grey:#6f6f6f;
}
*{margin:0;padding:0;box-sizing:border-box}
html,body{width:1200px;height:2773px;overflow:hidden;background:var(--white)}
body{position:relative;font-family:'Lato',sans-serif;color:var(--ink)}
.abs{position:absolute}

/* header */
.site-header{left:0;top:0;width:1200px;height:74px;background:var(--white);z-index:5}
.brand{left:172px;top:20px;font-weight:900;font-size:15px;color:var(--red);letter-spacing:.5px;line-height:34px;white-space:nowrap}
.main-nav{left:441px;top:29px;display:flex;gap:33px;font-size:14px;font-weight:700;color:var(--grey)}
.main-nav .active{color:var(--red)}
.call{left:861px;top:27px;font-size:16px;font-weight:700;color:var(--grey);display:flex;align-items:center;gap:8px}
.call b{color:var(--red)}

/* hero */
.hero{left:0;top:74px;width:1200px;height:566px;overflow:hidden}
.hero-photo{position:absolute;inset:0;background:linear-gradient(180deg,#8d939a 0%,#a9a6a2 35%,#6c6660 62%,#4b4c4d 100%)}
.hero-title{left:0;top:234px;width:1200px;text-align:center;font-size:40px;font-weight:900;color:var(--white);letter-spacing:.5px}
.btn{display:inline-block;background:var(--red);color:var(--white);font-weight:700;text-transform:uppercase;text-align:center}
.hero-btn{left:511px;top:298px;width:178px;height:40px;line-height:36px;border-radius:20px;font-size:13px;border:2px solid var(--white)}
.dots{left:512px;top:460px;display:flex;gap:4px}
.dots span{width:42px;height:4px;background:var(--white)}
.dots span.off{background:rgba(255,255,255,.5)}

/* headings */
.sec-title{left:0;width:1200px;text-align:center;font-size:30px;font-weight:900;color:var(--ink);text-transform:uppercase}
.sec-title em{font-style:normal;color:var(--red)}
.sec-lead{left:350px;width:500px;text-align:center;font-size:15px;line-height:23px;color:var(--grey)}

/* about */
.about-text{left:174px;top:843px;width:394px;font-size:12.5px;line-height:22.4px;color:var(--grey)}
.about-btn{top:1091px;height:29px;line-height:29px;font-size:11px;padding:0 14px}
.about-photo{left:597px;top:839px;width:429px;height:300px;border:1px solid #ddd;padding:5px;background:var(--white)}
.about-photo div{width:100%;height:100%;background:linear-gradient(180deg,#3a4250 0%,#c98a38 40%,#e8b55a 50%,#4a5060 70%,#2c3038 100%)}

/* why */
.why-bg{left:0;top:1266px;width:1200px;height:560px;background:linear-gradient(180deg,#f7f7f7 0%,#eeefed 55%,#dfe3dc 100%)}
.card{width:274px;height:274px;border-radius:50%;border:4px solid #cfcfcf;overflow:hidden;text-align:center;color:var(--white)}
.card-fill{position:absolute;inset:0}
.card h3{position:absolute;left:0;right:0;top:116px;font-size:28px;font-weight:900}
.card p{position:absolute;left:0;right:0;top:158px;font-size:11px;font-weight:700}

/* job profile */
.job-bg{left:0;top:1790px;width:1200px;height:594px;background:linear-gradient(180deg,#6d7688 0%,#c7c1a8 35%,#e9c98b 45%,#5f6a45 70%,#3b3e3f 100%)}
.job-panel{left:218px;top:1956px;width:764px;height:318px;background:rgba(255,255,255,.82)}
.job-text{left:350px;top:2076px;width:500px;text-align:center;font-size:15px;line-height:23.5px;color:var(--ink)}
.job-btn{left:553px;top:2189px;width:94px;height:27px;line-height:27px;font-size:11px}

/* footer */
.footer{left:0;top:2380px;width:1200px;height:393px;background:var(--dark);color:#d8d8d8}
.foot-brand{left:172px;top:2493px;font-size:19px;font-weight:900;color:var(--red);white-space:nowrap}
.foot-about{left:174px;top:2568px;width:270px;font-size:11.5px;line-height:19.5px;color:#d0d0d0}
.foot-col h4{font-size:15px;font-weight:700;color:var(--white);letter-spacing:.5px;margin-bottom:15px}
.foot-col li{list-style:none;font-size:13px;line-height:27.8px;color:#d0d0d0}
.news p{font-size:13px;line-height:20px;color:#d0d0d0;width:210px}
.news .field{margin-top:18px;width:210px;border-bottom:1px solid #777;font-size:11px;font-style:italic;color:#bbb;padding-bottom:6px}
.news .btn{margin-top:12px;width:92px;height:28px;line-height:28px;font-size:13px}
.foot-rule{left:172px;top:2694px;width:854px;height:1px;background:#444}
.social{left:172px;top:2716px;display:flex;gap:6px}
.social span{width:30px;height:30px;border-radius:50%;background:#111}
.copy{left:560px;top:2724px;width:466px;text-align:right;font-size:12.5px;color:#d8d8d8}
</style>
</head>
<body>

<header class="abs site-header">
  <div class="abs brand">RIDGELINE HAUL CARRIERS</div>
  <nav class="abs main-nav">
    <span class="active">HOME</span><span>ABOUT</span><span>SERVICES</span><span>JOBS</span><span>CONTACT</span>
  </nav>
  <div class="abs call">
    <svg width="14" height="14" viewBox="0 0 24 24"><path fill="#e52629" d="M6.6 10.8a15.1 15.1 0 0 0 6.6 6.6l2.2-2.2c.3-.3.7-.4 1-.2 1.1.4 2.3.6 3.6.6.6 0 1 .4 1 1V20c0 .6-.4 1-1 1A17 17 0 0 1 3 4c0-.6.4-1 1-1h3.5c.6 0 1 .4 1 1 0 1.3.2 2.5.6 3.6.1.3 0 .7-.2 1z"/></svg>
    <span>Call Us:<b>0491570110</b></span>
  </div>
</header>

<section class="abs hero">
  <div class="hero-photo" role="img" aria-label="Transport truck hauling drum containers on a flatbed trailer beside a brick warehouse"></div>
  <h1 class="abs hero-title">RIDGELINE HAUL CARRIERS</h1>
  <span class="abs btn hero-btn">Get Started Today</span>
  <div class="abs dots"><span></span><span></span><span class="off"></span><span></span></div>
  <svg class="abs" style="left:0;top:460px" width="1200" height="106" viewBox="0 0 1200 106">
    <polygon points="720,106 1200,72 1200,47" fill="#e52629"/>
    <polygon points="0,106 1200,74 1200,106" fill="#ffffff"/>
  </svg>
</section>

<section>
  <h2 class="abs sec-title" style="top:704px">About <em>Ridgeline Haul Carriers</em></h2>
  <p class="abs sec-lead" style="top:754px">Lorem ipsum dolor sit amet, consectetur adipiscing elit, sed do eiusmod tempor incididunt ut labore et dolore magna aliquad minim</p>
  <p class="abs about-text">Sed ut perspiciatis unde omnis iste natus error sit voluptatem accusantium doloremque laudantium, totam rem aperiam, eaque ipsa quae ab illo inventore veritatis et quasi architecto beatae vitae dicta sunt explicabo. Nemo enim ipsam voluptatem quia voluptas sit aspernatur aut odit aut fugit, sed quia consequuntur magni dolores eos qui ratione voluptatem sequi nesciunt. Neque porro quisquam est, qui dolorem ipsum quia dolor sit amet, consectetur, adipisci velit, sed quia non numquam eius modi tempora incidunt ut labore et dolore magnam Sed ut perspiciatis unde omnis iste natus error sit voluptatem accusantium doloremque laudantium, totam rem aperiam, eaque ipsa quae ab illo invquia consequuntur magni dolore.</p>
  <span class="abs btn about-btn" style="left:172px">Read More</span>
  <span class="abs btn about-btn" style="left:272px;background:var(--btn-grey)">View Our Drivers</span>
  <div class="abs about-photo"><div role="img" aria-label="Two trucks driving on a highway at sunset"></div></div>
</section>

<section>
  <div class="abs why-bg" role="img" aria-label="Faded landscape of hills and trees behind the section"></div>
  <h2 class="abs sec-title" style="top:1298px">Why <em>Choose Us?</em></h2>
  <p class="abs sec-lead" style="top:1348px">Lorem ipsum dolor sit amet, consectetur adipiscing elit, sed do eiusmod tempor incididunt ut labore et dolore magna aliquad minim</p>
  <div class="abs card" style="left:172px;top:1420px">
    <div class="card-fill" role="img" aria-label="Drum containers loaded on a trailer" style="background:linear-gradient(180deg,#4a4f55,#2f3a30 60%,#3a3c3e)"></div>
    <h3>MATERIALS</h3><p>READ MORE</p>
  </div>
  <div class="abs card" style="left:462px;top:1420px">
    <div class="card-fill" role="img" aria-label="Truck driver standing in front of trucks" style="background:linear-gradient(180deg,#7a8088,#5a5c60 55%,#6a3a38)"></div>
    <h3>SERVICES</h3><p>READ MORE</p>
  </div>
  <div class="abs card" style="left:752px;top:1420px">
    <div class="card-fill" role="img" aria-label="Trucks on a highway lined with trees" style="background:linear-gradient(180deg,#5d6670,#3c4a3a 55%,#3b3d40)"></div>
    <h3>TRUCKS</h3><p>READ MORE</p>
  </div>
</section>

<section>
  <div class="abs job-bg" role="img" aria-label="Truck on a country road with the sun low over fields"></div>
  <svg class="abs" style="left:0;top:1790px" width="1200" height="56" viewBox="0 0 1200 56">
    <polygon points="0,0 1200,0 1200,10 0,0" fill="#dfe3dc"/>
    <polygon points="0,0 1200,10 1200,36 700,40" fill="#dfe3dc"/>
    <polygon points="700,40 1200,32 1200,14" fill="#e52629"/>
  </svg>
  <div class="abs job-panel"></div>
  <h2 class="abs sec-title" style="top:2025px">Job <em>Profile</em></h2>
  <p class="abs job-text">Lorem ipsum dolor sit amet, consectetur adipiscing elit, sed do eiusmod tempor incididunt ut laLorem ipsum dolor sit amet, consectetur adipiscing elit, sed do eiusmod tempor incididunt ut labore et dolore magna aliquad minimbore et dolore magna aliquad minimLorem ipsum dolor.</p>
  <span class="abs btn job-btn">Apply Now</span>
</section>

<footer class="abs footer"></footer>
<svg class="abs" style="left:0;top:2378px" width="1200" height="48" viewBox="0 0 1200 48">
  <polygon points="0,2 600,2 0,46" fill="#e52629"/>
</svg>
<div class="abs foot-brand">RIDGELINE HAUL CARRIERS</div>
<p class="abs foot-about">Morbi pharetra blandit faucibureeros turpis, sceler isque in nisl anatis blandit sem. Cras quis dui vitae puus interdum sollicitudin ut ut odiolerisqu ein nisl anatis blandit semas quis du</p>
<div class="abs foot-col" style="left:495px;top:2478px">
  <h4>NAV</h4>
  <ul><li>Home</li><li>About</li><li>Services</li><li>Jobs</li><li>Contact</li></ul>
</div>
<div class="abs foot-col" style="left:627px;top:2478px">
  <h4>LINKS</h4>
  <ul><li>Sed ut perspiciatis</li><li>Unde omnis isteatus</li><li>Voluptatem accsan</li><li>Tium doloreque</li><li>Haudantium</li></ul>
</div>
<div class="abs foot-col news" style="left:818px;top:2478px">
  <h4>NEWSLETTER</h4>
  <p>Subscribe to us to get and receive the latest news, sales and updates.</p>
  <div class="field">Email Address</div>
  <span class="btn">Sign Up</span>
</div>
<div class="abs foot-rule"></div>
<div class="abs social"><span></span><span></span><span></span><span></span></div>
<p class="abs copy">© 2019 Ridgeline Haul Carriers All rights are reserved. Privacy | Terms of use</p>

</body>
</html>
```